Website design for legal tech start up in Switzerland (B2B)

We are for a legal tech start up in Switzerland called KOVA. We have been running since August 2016. This will be our first live website.

We need a website designed and business card design for our start-up in Switzerland. We also need the Web design to be converted into HTML and CSS files.

Function of website:
• To inform potential customers of our services
• Form a key part of our digital marketing and sales footprint.
• Branding

Please find attached logo.
Updates

Project Deadline Extended Reason: Giving us time to review submissions and provide opportunity for more submissions. Added Thursday, February 16, 2017

Project Deadline Extended
Reason: Looking for more idea's not necessarily set on blue and grey colours only.

Target Market(s)

B2B tech powered legal services.

Industry/Entity Type

Legal

Contact Information for Business Card

Lean and slick design.

Coding

Coded - Design and coding required

Number of Pages Required

5+ page

Requirements
Must have
• VERY LEAN AND CLEAN DESIGN!
• We have received many great standard designs, but we are looking for something more out-of-the box: You can get inspiration from these designs: http://www.pixelvane.com/websites/clean/
• Thanks!!
• Easy content management system
• Well structured coding for additional development
• Responsive webpage for all types of devices
• SEO optimized
• Tabs (Home, services, team, careers, blog, contact us)
• Colour scheme complementary to logo
Nice to have
• Look and Design - Approachable, High-tech, Modern
• Easy to add chat bot capability in future
Should not have
• Too busy/ too much clutter
• Not take to long to load

```html
<!DOCTYPE html>
<html lang="en">
<head>
<meta charset="utf-8">
<title>KOVA – Legal Tech Services</title>
<link rel="stylesheet" href="https://fonts.googleapis.com/css2?family=Raleway:wght@400;600&family=Tinos:wght@400;700&family=Arimo:ital,wght@0,400;0,700;1,400&display=swap">
<style>
:root{
  --navy:#1d4a82;
  --navy-dark:#17355f;
  --navy-deep:#112846;
  --ink:#222;
  --grey-text:#555;
  --logo-grey:#3a3a3c;
  --rule:#c9c9c9;
  --footer-bar:#3b3b3b;
  --white:#fff;
}
*{box-sizing:border-box;margin:0;padding:0}
html,body{width:1200px;height:2510px;overflow:hidden;background:var(--white)}
.canvas{position:relative;width:1200px;height:2510px;overflow:hidden;font-family:"Arimo",Arial,sans-serif;color:var(--ink)}
.abs{position:absolute}

/* header */
.header{position:absolute;left:0;top:0;width:1200px;height:104px;background:var(--white)}
.brand{position:absolute;left:160px;top:22px;font-family:"Raleway",sans-serif;font-weight:600;font-size:66px;letter-spacing:4px;color:var(--logo-grey);line-height:1}
.call-pill{position:absolute;left:722px;top:0;width:478px;height:34px;background:#e6e6e6;border-bottom-left-radius:22px;display:flex;align-items:center;padding-left:34px;gap:10px;font-size:13px;color:#333}
.icon-dot{display:inline-block;width:24px;height:24px;border-radius:50%;background:var(--navy-dark)}
.call-pill .social{display:flex;gap:5px;margin-left:18px}
.cta{position:absolute;left:795px;top:54px;width:235px;height:42px;background:var(--navy);border-radius:3px;color:var(--white);font-family:"Tinos",serif;font-size:15px;display:flex;align-items:center;justify-content:center;letter-spacing:.3px}

.nav{position:absolute;left:0;top:104px;width:1200px;height:43px;background:linear-gradient(var(--navy),var(--navy-dark));font-family:"Tinos",serif;font-size:14px;color:var(--white)}
.nav a{position:absolute;top:13px;color:var(--white);text-decoration:none}
.nav .sep{position:absolute;top:0;width:1px;height:43px;background:rgba(255,255,255,.18)}
.nav .follow{position:absolute;left:786px;top:13px}
.nav .social{position:absolute;left:898px;top:9px;display:flex;gap:5px}
.nav .social span{width:24px;height:24px;border-radius:50%;border:1.5px solid rgba(255,255,255,.7)}

/* hero */
.hero{position:absolute;left:0;top:147px;width:1200px;height:503px;background:linear-gradient(180deg,#0b1420 0%,#1a2433 45%,#3a3326 75%,#0a0c10 100%)}
.hero-caption{position:absolute;left:0;top:595px;width:1200px;text-align:center;font-family:"Raleway",sans-serif;font-size:35px;color:var(--white)}
.hero-arrow{position:absolute;top:376px;width:22px;height:26px;background:#3a3a3a;border:1px solid #888}

/* welcome */
.section-title{position:absolute;left:0;width:1200px;text-align:center;font-family:"Tinos",serif;font-size:33px;color:#111}
.title-rule{position:absolute;left:465px;width:270px;height:1px;background:var(--rule)}
.title-rule::after{content:"";position:absolute;left:117px;top:-1px;width:36px;height:3px;background:var(--navy)}
.welcome-text{position:absolute;left:178px;top:756px;width:844px;text-align:center;font-family:"Tinos",serif;font-size:11.3px;line-height:19.5px;color:#333}

/* why choose us */
.why{position:absolute;left:0;top:1398px;width:1200px;height:435px;background:linear-gradient(180deg,var(--navy) 0%,var(--navy-dark) 55%,var(--navy-deep) 100%)}
.why-title{position:absolute;left:0;top:46px;width:1200px;text-align:center;font-family:"Tinos",serif;font-size:27px;color:var(--white)}
.why-rule{position:absolute;left:505px;top:88px;width:190px;height:1px;background:rgba(255,255,255,.4)}
.reason{position:absolute;color:var(--white);font-family:"Tinos",serif}
.reason h3{font-weight:400;font-size:15.5px;line-height:19px}
.reason p{font-size:11.5px;line-height:18px;margin-top:3px}
.reason.left{text-align:right}
.why-brand{position:absolute;left:0;top:360px;width:1200px;text-align:center;font-family:"Raleway",sans-serif;font-weight:600;font-size:64px;letter-spacing:4px;color:var(--logo-grey);line-height:1}

/* testimonials */
.testimonial{position:absolute;left:220px;top:1974px;width:760px;text-align:center;font-family:"Arimo",sans-serif;font-style:italic;font-size:13.5px;line-height:25px;color:#222}
.quote-mark{position:absolute;font-family:"Tinos",serif;font-size:44px;color:#bbb;line-height:1}
.client{position:absolute;left:0;width:1200px;text-align:center;font-size:14px}
.dots{position:absolute;left:574px;top:2134px;display:flex;gap:8px}
.dots span{width:9px;height:9px;border-radius:50%;background:#bbb}
.dots span.on{background:var(--navy)}

/* footer */
.footer{position:absolute;left:0;top:2183px;width:1200px;height:281px;background:linear-gradient(180deg,var(--navy) 0%,var(--navy-dark) 100%);color:var(--white);font-family:"Tinos",serif}
.footer h4{position:absolute;font-weight:400;font-size:17px}
.quick-links{position:absolute;left:164px;top:82px;list-style:none;font-size:12.5px;line-height:21.5px}
.quick-links li::before{content:"› ";}
.contact-row{position:absolute;left:316px;display:flex;gap:10px;font-size:12.5px;line-height:19px}
.contact-row .ic{flex:none;width:18px;height:18px;border-radius:50%;background:var(--white)}
.field{position:absolute;left:564px;width:207px;background:var(--white);border-radius:2px;color:#444;font-family:"Arimo",sans-serif;font-size:11px;padding:8px 7px}
.submit{position:absolute;left:564px;top:229px;width:102px;height:32px;background:#0c0c0c;color:var(--white);font-size:15px;display:flex;align-items:center;justify-content:center;gap:10px}
.footer .social{position:absolute;left:922px;top:90px;display:flex;gap:5px}
.footer .social span{width:24px;height:24px;border-radius:50%;background:var(--white)}
.footer-brand{position:absolute;left:917px;top:160px;font-family:"Raleway",sans-serif;font-weight:600;font-size:38px;letter-spacing:2px;color:rgba(255,255,255,.72);line-height:1}
.copyright{position:absolute;left:0;top:2464px;width:1200px;height:46px;background:var(--footer-bar);color:#ddd;font-family:"Tinos",serif;font-size:12px;display:flex;align-items:center;justify-content:center}
</style>
</head>
<body>
<div class="canvas">

  <header class="header">
    <div class="brand">KOVA</div>
    <div class="call-pill">
      <svg width="24" height="24" viewBox="0 0 24 24"><circle cx="12" cy="12" r="12" fill="#17355f"/><path d="M8 6.5l2 0 1 3-1.4 1a7 7 0 0 0 3.9 3.9l1-1.4 3 1v2a1.5 1.5 0 0 1-1.6 1.5A10 10 0 0 1 6.5 8.1 1.5 1.5 0 0 1 8 6.5z" fill="#fff"/></svg>
      <span>Call : 555-014-2290</span>
      <span class="social"><span class="icon-dot"></span><span class="icon-dot"></span><span class="icon-dot"></span><span class="icon-dot"></span></span>
    </div>
    <div class="cta">GET A FREE CONSULTATION</div>
  </header>

  <nav class="nav">
    <span class="sep" style="left:160px"></span>
    <a style="left:186px">Home</a>
    <a style="left:273px">Services</a>
    <a style="left:373px">Team</a>
    <a style="left:457px">Careers</a>
    <a style="left:553px">Blog</a>
    <a style="left:632px">Contact Us</a>
    <span class="sep" style="left:756px"></span>
    <span class="follow">Follow Us On</span>
    <span class="social"><span></span><span></span><span></span><span></span></span>
  </nav>

  <section class="hero" role="img" aria-label="Night city skyline with light trails of traffic on a curving highway"></section>
  <div class="hero-arrow" style="left:4px"><svg width="20" height="24"><path d="M12 8l-4 4 4 4" stroke="#fff" stroke-width="2" fill="none"/></svg></div>
  <div class="hero-arrow" style="left:1162px"><svg width="20" height="24"><path d="M8 8l4 4-4 4" stroke="#fff" stroke-width="2" fill="none"/></svg></div>
  <div class="hero-caption">Helping Technology Companies Succeed</div>

  <h1 class="section-title" style="top:680px">Welcome to KOVA</h1>
  <div class="title-rule" style="top:735px"></div>
  <p class="welcome-text">Lorem ipsum dolor sit amet, consectetuer adipiscing elit, sed diam nonummy nibh euismod tincidunt ut laoreet dolore magna aliquam erat volutpat. Ut wisi enim ad minim veniam, quis nostrud exerci tation ullamcorper suscipit lobortis nisl ut aliquip ex ea commodo consequat. Duis autem vel eum iriure dolor in hendrerit in vulputate velit esse molestie consequat, vel illum dolore eu feugiat nulla facilisis at vero eros et accu nonummy nibh euismod tincidunt ut laoreet dolore magna aliquam erat volutpat. Ut wisi enim ad minim veniam, quis nostrud exerci tation ullamcorper suscipit lobortis nisl ut aliquip ex ea commodo consequat. Duis autmean et iusto odio dignissim qui blandit praesent luptatum zzril delenit augue duis dolore te feugait nulla facilisi.</p>

  <svg class="abs services" style="left:0;top:905px" width="1200" height="450" viewBox="0 0 1200 450">
    <defs>
      <polygon id="hex-outer" points="0,-118 102.2,-59 102.2,59 0,118 -102.2,59 -102.2,-59"/>
      <polygon id="hex-inner" points="0,-106 91.8,-53 91.8,53 0,106 -91.8,53 -91.8,-53"/>
      <linearGradient id="g-info" x1="0" y1="0" x2="1" y2="1"><stop offset="0" stop-color="#dfe6ec"/><stop offset="1" stop-color="#6f8aa3"/></linearGradient>
      <linearGradient id="g-case" x1="0" y1="0" x2="1" y2="1"><stop offset="0" stop-color="#9fb4c8"/><stop offset="1" stop-color="#3e5f82"/></linearGradient>
      <linearGradient id="g-app" x1="0" y1="0" x2="1" y2="1"><stop offset="0" stop-color="#2f4c72"/><stop offset="1" stop-color="#0f1d33"/></linearGradient>
      <linearGradient id="g-env" x1="0" y1="0" x2="0" y2="1"><stop offset="0" stop-color="#8fbf5a"/><stop offset="1" stop-color="#2e5a1e"/></linearGradient>
      <linearGradient id="g-legal" x1="0" y1="0" x2="1" y2="1"><stop offset="0" stop-color="#6b4a36"/><stop offset="1" stop-color="#2a1d16"/></linearGradient>
      <linearGradient id="g-proc" x1="0" y1="0" x2="1" y2="1"><stop offset="0" stop-color="#d8d8d8"/><stop offset="1" stop-color="#6a6a6a"/></linearGradient>
    </defs>
    <g fill="#e2e2e2" stroke="#d0d0d0" stroke-width="6" stroke-linejoin="round">
      <use href="#hex-outer" x="377" y="125"/><use href="#hex-outer" x="603" y="125"/><use href="#hex-outer" x="824" y="125"/>
      <use href="#hex-outer" x="263" y="322"/><use href="#hex-outer" x="489" y="322"/><use href="#hex-outer" x="712" y="322"/><use href="#hex-outer" x="938" y="322"/>
    </g>
    <g stroke-linejoin="round" stroke-width="6" font-family="Tinos, serif" font-weight="700" font-size="14" fill="#fff" text-anchor="middle">
      <g role="img" aria-label="Hands reviewing printed charts and data reports"><use href="#hex-inner" x="377" y="125" fill="url(#g-info)" stroke="#f4f4f4"/></g>
      <text x="377" y="197">Information Management</text>
      <use href="#hex-inner" x="603" y="125" fill="#1d4a82" stroke="#1d4a82"/>
      <text x="603" y="112" font-weight="400" font-size="38">Our</text>
      <text x="603" y="154" font-weight="400" font-size="38">Services</text>
      <g role="img" aria-label="Business professional on the phone at a desk"><use href="#hex-inner" x="824" y="125" fill="url(#g-case)" stroke="#f4f4f4"/></g>
      <text x="824" y="197">Case Support</text>
      <g role="img" aria-label="Hand touching a digital network of device icons"><use href="#hex-inner" x="263" y="322" fill="url(#g-app)" stroke="#f4f4f4"/></g>
      <text x="263" y="383">Application Development</text>
      <g role="img" aria-label="Green forest canopy seen from below"><use href="#hex-inner" x="489" y="322" fill="url(#g-env)" stroke="#f4f4f4"/></g>
      <text x="489" y="383">Environmental Litigation</text>
      <g role="img" aria-label="Person signing legal documents at a desk"><use href="#hex-inner" x="712" y="322" fill="url(#g-legal)" stroke="#f4f4f4"/></g>
      <text x="712" y="383">Legal Word Processing</text>
      <g role="img" aria-label="Steel ball bearings on technical paperwork"><use href="#hex-inner" x="938" y="322" fill="url(#g-proc)" stroke="#f4f4f4"/></g>
      <text x="938" y="383">Procurement Support</text>
    </g>
  </svg>

  <section class="why">
    <h2 class="why-title">Why Choose Us</h2>
    <div class="why-rule"></div>
    <svg class="abs" style="left:0;top:0" width="1200" height="435" viewBox="0 0 1200 435">
      <circle cx="600" cy="435" r="168" fill="#fff" stroke="#2f6fc0" stroke-width="6"/>
      <g stroke="#fff" stroke-width="1.5">
        <line x1="439" y1="382" x2="372" y2="360"/><line x1="482" y1="313" x2="430" y2="259"/><line x1="554" y1="271" x2="536" y2="206"/>
        <line x1="646" y1="271" x2="665" y2="206"/><line x1="718" y1="313" x2="767" y2="259"/><line x1="761" y1="382" x2="820" y2="360"/>
      </g>
      <g fill="#fff" stroke="#1d4a82" stroke-width="2">
        <circle cx="439" cy="382" r="6"/><circle cx="482" cy="313" r="6"/><circle cx="554" cy="271" r="6"/>
        <circle cx="646" cy="271" r="6"/><circle cx="718" cy="313" r="6"/><circle cx="761" cy="382" r="6"/>
      </g>
      <g fill="#fff">
        <circle cx="372" cy="360" r="37"/><circle cx="430" cy="259" r="37"/><circle cx="536" cy="206" r="37"/>
        <circle cx="665" cy="206" r="37"/><circle cx="767" cy="259" r="37"/><circle cx="820" cy="360" r="37"/>
      </g>
      <g fill="#1d4a82">
        <!-- lightbulb -->
        <circle cx="372" cy="354" r="10"/><rect x="366" y="365" width="12" height="8" rx="2"/>
        <!-- gear -->
        <circle cx="430" cy="259" r="11"/><circle cx="430" cy="259" r="4" fill="#fff"/>
        <g stroke="#1d4a82" stroke-width="5"><line x1="430" y1="243" x2="430" y2="275"/><line x1="414" y1="259" x2="446" y2="259"/><line x1="419" y1="248" x2="441" y2="270"/><line x1="441" y1="248" x2="419" y2="270"/></g>
        <circle cx="430" cy="259" r="4" fill="#fff"/>
        <!-- phone with bubble -->
        <path d="M523 196l5 0 2.5 7-3.5 2.5a16 16 0 0 0 9 9l2.5-3.5 7 2.5v5a3 3 0 0 1-3.2 3A24 24 0 0 1 520 199a3 3 0 0 1 3-3z"/>
        <circle cx="547" cy="194" r="8"/>
        <!-- person with alert -->
        <circle cx="660" cy="200" r="9"/><path d="M645 226a15 13 0 0 1 30 0z"/><circle cx="677" cy="196" r="8"/><rect x="676" y="191" width="2" height="6" fill="#fff"/>
        <!-- calendar with clock -->
        <rect x="752" y="246" width="26" height="24" rx="2"/><rect x="755" y="254" width="20" height="13" fill="#fff"/><circle cx="779" cy="270" r="8"/><path d="M779 265v5h4" stroke="#fff" stroke-width="1.5" fill="none"/>
        <!-- people -->
        <circle cx="813" cy="351" r="7"/><circle cx="828" cy="351" r="7"/><path d="M802 374a11 11 0 0 1 22 0z"/><path d="M817 374a11 11 0 0 1 22 0z"/>
      </g>
    </svg>
    <div class="reason left" style="right:721px;top:120px;width:240px"><h3>Unbiased Recommendations</h3><p>Lorem ipsum dolor sit mork<br>[+]...adipiscing sed diam</p></div>
    <div class="reason left" style="right:825px;top:206px;width:200px"><h3>Unparalleled<br>Service</h3><p>Lorem ipsum dolor sit mork<br>[+]...adipiscing sed diam</p></div>
    <div class="reason left" style="right:879px;top:334px;width:200px"><h3>Superior Advice</h3><p>Lorem ipsum dolor sit mork<br>[+]...adipiscing sed diam</p></div>
    <div class="reason" style="left:721px;top:120px;width:240px"><h3>Expert Guidance</h3><p>Lorem ipsum dolor sit mork<br>adipiscing sed diam...[+]</p></div>
    <div class="reason" style="left:825px;top:218px;width:220px"><h3>Considerable Time<br>For You</h3><p>Lorem ipsum dolor sit mork<br>adipiscing sed diam...[+]</p></div>
    <div class="reason" style="left:879px;top:316px;width:220px"><h3>Deep Legal Industry<br>Relationships</h3><p>Lorem ipsum dolor sit mork<br>adipiscing sed diam...[+]</p></div>
    <div class="why-brand">KOVA</div>
  </section>

  <h2 class="section-title" style="top:1900px;font-size:27px">Clients <span style="color:var(--navy)">Testimonials</span></h2>
  <div class="title-rule" style="top:1944px;left:478px;width:244px"></div>
  <svg class="abs" style="left:134px;top:1996px" width="28" height="56"><path d="M24 2L4 28l20 26" stroke="#c8c8c8" stroke-width="2" fill="none"/></svg>
  <svg class="abs" style="left:1038px;top:1996px" width="28" height="56"><path d="M4 2l20 26L4 54" stroke="#c8c8c8" stroke-width="2" fill="none"/></svg>
  <span class="quote-mark" style="left:193px;top:1966px">“</span>
  <p class="testimonial">Lorem ipsum dolor sit amet, consectetuer adipiscing elit, sed diam nonummy nibh euismod tinciduntol ut laoreet dolore magna aliquam erat volutpat. Ut wisi enim ad minim veniam, quis nostrud exercimori mornkle tation ullamcorper suscipit lobortis nisl ut aliquip ex ea commodo consequat.</p>
  <span class="quote-mark" style="left:770px;top:2034px">”</span>
  <div class="client" style="top:2071px;color:var(--navy)">Marla V.</div>
  <div class="client" style="top:2091px;font-size:13px">Lugano, TI</div>
  <div class="dots"><span class="on"></span><span></span><span></span><span></span></div>

  <footer class="footer">
    <h4 style="left:164px;top:47px">Quick Links</h4>
    <ul class="quick-links"><li>Home</li><li>Services</li><li>Team</li><li>Careers</li><li>Blog</li><li>Contact Us</li></ul>

    <h4 style="left:316px;top:47px">Contact Details</h4>
    <div class="contact-row" style="top:85px"><span class="ic"></span><span>Kova Technology<br>Street Name City Name<br>State Zipcode</span></div>
    <div class="contact-row" style="top:157px"><span class="ic"></span><span>555-014-2290</span></div>
    <div class="contact-row" style="top:190px"><span class="ic"></span><span>555-014-2290</span></div>
    <div class="contact-row" style="top:226px"><span class="ic"></span><span>inquiry@kovatechnology.com</span></div>

    <h4 style="left:564px;top:47px">Quick Inquiry</h4>
    <div class="field" style="top:87px;height:32px">Name</div>
    <div class="field" style="top:125px;height:31px">Email</div>
    <div class="field" style="top:160px;height:62px">Message</div>
    <div class="submit">Submit <svg width="16" height="10"><path d="M0 5h14M10 1l4 4-4 4" stroke="#fff" stroke-width="1.3" fill="none"/></svg></div>

    <h4 style="left:932px;top:53px">Follow Us</h4>
    <div class="social"><span></span><span></span><span></span><span></span></div>
    <div class="footer-brand">KOVA</div>
  </footer>
  <div class="copyright">Copyright © 2017 Kova Technology. All Rights Reserved.</div>

</div>
</body>
</html>
```